Bloom Path! A website showcasing who I am as a person

Bloom Path started out as idea for me to better myself as a person and work on small projects that would help me grow as a person. Now I want to build a website showcasing "Bloom Path." I want the website to showcase who I am and how I have grown both professionally and personally. I can build the raw code of the website on my own but I am not really much of a designer. I am looking for a design where I can write and post blogs, articles and share my thoughts. A little about myself and the ideas and interests that I want to share
What is Bloom Path
Who I am
Background - Professional
Brand Marketing
Email Automation
Hiking
Rock Climbing
Traveling
Exercising and Transformation
"Personal Thoughts"
Hopefully this is enough information to get people started on some designs.
Work
3 page

```html
<!DOCTYPE html>
<html lang="en">
<head>
<meta charset="utf-8">
<title>Arin Solano — Bloom Path</title>
<link rel="stylesheet" href="https://fonts.googleapis.com/css2?family=Montserrat:wght@700&family=Lato:wght@400;700&family=Open+Sans:wght@400;600;700&display=swap">
<style>
:root{
  --blue:#2f6fb6;
  --blue-dark:#245c9c;
  --title-blue:#2b6cb2;
  --ink:#333;
  --muted:#555;
  --panel:#f5f5f5;
  --section-grey:#f2f2f2;
  --footer:#4a4a4a;
  --white:#fff;
  --btn-dark:#2b2b2b;
}
*{box-sizing:border-box;margin:0;padding:0}
html,body{width:1200px;height:3557px;overflow:hidden;background:var(--white)}
body{font-family:"Open Sans",Arial,sans-serif;color:var(--ink)}
.page{position:relative;width:1200px;height:3557px;overflow:hidden}
.abs{position:absolute}

/* header */
.topbar{left:0;top:0;width:1200px;height:88px;background:var(--white)}
.brand{left:100px;top:28px;font-family:"Montserrat",Arial,sans-serif;font-weight:700;font-size:27px;color:var(--blue);letter-spacing:.5px;white-space:nowrap}
.topnav{right:100px;top:34px;display:flex;gap:30px;font-size:14px;font-weight:600;color:#222;text-transform:uppercase;white-space:nowrap}
.mainnav{left:0;top:88px;width:1200px;height:54px;background:var(--blue);z-index:2}
.mainnav ul{list-style:none;display:flex;justify-content:space-between;width:1000px;margin-left:100px}
.mainnav li{display:block;height:54px;line-height:54px;padding:0 22px;color:var(--white);font-size:13px;font-weight:600;text-transform:uppercase;white-space:nowrap}
.mainnav li.active{background:var(--blue-dark)}

/* hero */
.hero{left:0;top:142px;width:1200px;height:560px}
.hero-photo{position:absolute;inset:0;background:linear-gradient(180deg,#7f9fc0 0%,#b9bcb5 30%,#e8b770 50%,#5a4630 72%,#1e1a14 100%)}
.hero-title{left:114px;top:220px;font-weight:700;font-size:40px;line-height:50px;color:var(--white);white-space:nowrap;z-index:1}
.hero-sub{left:114px;top:284px;width:390px;font-size:19px;font-weight:600;color:var(--white);line-height:28px;z-index:1}
.hero-btn{left:114px;top:366px;width:160px;height:52px;border:2px solid var(--white);color:var(--white);font-size:15px;font-weight:600;text-align:center;line-height:48px;text-transform:uppercase;white-space:nowrap;z-index:1}
.dots{left:116px;top:440px;display:flex;gap:5px;z-index:1}
.dots span{width:12px;height:12px;border-radius:50%;background:#ddd}
.dots span:first-child{background:var(--blue)}

/* section titles */
.sec-title{left:0;width:1200px;text-align:center;font-family:"Lato",Arial,sans-serif;font-weight:700;font-size:27px;color:var(--title-blue);text-transform:uppercase;letter-spacing:.5px}
.sec-rule{left:550px;width:100px;height:2px;background:var(--blue)}
.lead{left:120px;width:960px;text-align:center;font-size:13px;line-height:23px;color:var(--muted)}
.btn-blue{background:var(--blue);color:var(--white);font-size:14px;font-weight:600;text-align:center;text-transform:uppercase;white-space:nowrap}

/* about */
.about-bg{left:0;top:676px;width:1200px;height:500px}

/* fields */
.field-photo{height:253px}
.field-cap{height:104px;background:var(--white);border:1px solid #ccc;text-align:center;padding-top:8px}
.field-cap h3{font-family:"Lato",Arial,sans-serif;font-size:17px;font-weight:700;color:#222;text-transform:uppercase;margin-bottom:10px;white-space:nowrap}
.field-cap p{font-size:13px;line-height:20px;color:var(--muted)}
.field-cap.featured{background:var(--blue);border-color:var(--blue)}
.field-cap.featured h3,.field-cap.featured p{color:var(--white)}

/* blog */
.blog-panel{left:100px;top:1786px;width:676px;height:1004px;background:var(--panel)}
.side-panel{left:790px;top:1786px;width:308px;height:1004px;background:var(--panel)}
.panel-title{font-family:"Lato",Arial,sans-serif;font-weight:700;font-size:23px;color:var(--title-blue);text-transform:uppercase;white-space:nowrap}
.post-photo{width:308px;height:228px}
.post-tag{position:absolute;left:0;bottom:0;height:44px;line-height:44px;padding:0 12px;font-size:17px;color:var(--white);white-space:nowrap}
.post-tag.blue{background:rgba(47,111,182,.88);width:182px}
.post-tag.dark{background:rgba(20,20,20,.75);width:182px}
.post-meta{display:flex;gap:16px;font-size:10.5px;font-weight:700;color:var(--blue);align-items:center;white-space:nowrap}
.post-meta span{display:flex;align-items:center;gap:4px}
.post-text{width:308px;font-size:11.5px;line-height:16px;color:var(--muted)}
.read-btn{width:94px;height:31px;line-height:31px;font-size:12px;font-weight:700;color:var(--white);text-align:center}
.read-btn.blue{background:var(--blue)}
.read-btn.dark{background:var(--btn-dark)}
.pager{left:119px;top:2742px;display:flex;gap:5px}
.pager span{height:33px;line-height:33px;padding:0 12px;background:#a9a9a9;color:var(--white);font-size:14px;font-weight:700;white-space:nowrap}
.pager span.on{background:var(--blue)}

.side-photo{left:828px;width:237px;height:154px}
.side-text{left:828px;width:240px;font-size:13px;font-weight:700;line-height:23px;color:#222}
.side-date{left:828px;font-size:12px;font-weight:700;color:var(--blue);display:flex;align-items:center;gap:6px;white-space:nowrap}
.social{left:842px;top:2740px;display:flex;gap:8px}
.social span{width:38px;height:38px;border-radius:50%}

/* subscribe */
.subscribe-rule{left:100px;top:2900px;width:1000px;height:3px;background:var(--blue)}
.email-input{left:159px;top:3065px;width:709px;height:48px;border:1px solid #ccc;background:var(--white);font-size:14px;color:#444;padding-left:16px;line-height:46px}
.subscribe-btn{left:880px;top:3065px;width:159px;height:48px;line-height:48px}

/* footer */
.footer-shape{left:0;top:3170px;width:1200px;height:387px}
.footer-brand{left:0;top:3310px;width:1200px;text-align:center;font-family:"Montserrat",Arial,sans-serif;font-weight:700;font-size:25px;color:var(--white)}
.footer-links{left:0;top:3406px;width:1200px;text-align:center;font-size:16px;font-weight:600;color:var(--white);white-space:nowrap}
.footer-links i{font-style:normal;margin:0 24px}
.footer-rule{left:100px;top:3470px;width:1000px;height:1px;background:#8a8a8a}
.copyright{left:100px;top:3505px;font-size:14px;font-weight:600;color:var(--white);white-space:nowrap}
.footer-social{left:910px;top:3497px;display:flex;gap:9px}
.footer-social span{width:34px;height:34px;border-radius:50%;border:2px solid var(--white)}
</style>
</head>
<body>
<div class="page">

  <header>
    <div class="abs topbar"></div>
    <div class="abs brand">ARIN SOLANO</div>
    <nav class="abs topnav"><span>Traveling</span><span>Exercising and Transformation</span><span>"Personal Thoughts"</span><span>Rock Climbing</span></nav>
    <nav class="abs mainnav">
      <ul><li class="active">What is Bloom Path</li><li>Who I am</li><li>Background - Professional</li><li>Brand Marketing</li><li>Email Automation</li><li>Hiking</li></ul>
    </nav>
  </header>

  <section class="abs hero">
    <div class="hero-photo" role="img" aria-label="Hiker with backpack and trekking poles on a mountain ridge at sunset"></div>
    <svg class="abs" style="left:100px;top:52px" width="610" height="300" viewBox="0 0 610 300" aria-hidden="true">
      <polygon points="0,0 605,0 300,300 0,300" fill="rgba(40,50,65,.5)"/>
    </svg>
    <svg class="abs" style="left:0;top:430px" width="1200" height="130" viewBox="0 0 1200 130" aria-hidden="true">
      <polygon points="0,60 540,130 1200,45 1200,130 0,130" fill="#f2f2f2"/>
      <polygon points="0,58 160,80 160,86 0,66" fill="var(--blue)"/>
      <polygon points="760,84 1000,55 1000,60 760,92" fill="var(--blue)"/>
    </svg>
  </section>
  <h1 class="abs hero-title">"BLOOM PATH"</h1>
  <p class="abs hero-sub">Who I am and how I have grown both professionally and personally.</p>
  <div class="abs hero-btn">Find out more</div>
  <div class="abs dots"><span></span><span></span><span></span><span></span><span></span></div>

  <section>
    <svg class="abs about-bg" width="1200" height="500" viewBox="0 0 1200 500" aria-hidden="true">
      <polygon points="0,24 1200,24 1200,370 880,430 355,475 0,370" fill="var(--section-grey)"/>
      <polygon points="210,425 355,475 350,478 205,432" fill="var(--blue)"/>
      <polygon points="760,444 990,420 990,426 770,450" fill="var(--blue)"/>
    </svg>
    <h2 class="abs sec-title" style="top:760px">What is Bloom Path</h2>
    <div class="abs sec-rule" style="top:812px"></div>
    <p class="abs lead" style="top:856px">Nemo enim ipsam voluptatem quia voluptas sit aspernatur aut odit aut fugit, sed quia consequuntur magni dolores eos qui ratione voluptatem sequi nesciunt. Neque porro quisquam est, qui dolorem ipsum quia dolor sit amet, consectetur, adipisci velit, sed quia non numquam eius modi tempora incidunt ut labore et dolore magnam aliquam quaerat voluptatem. Ut enim ad minima veniam, quis nostrum exercitationem ullam corporis suscipit laboriosam, nisi ut aliquid ex ea commodi consequatur.</p>
    <div class="abs btn-blue" style="left:536px;top:994px;width:130px;height:47px;line-height:47px">Read more</div>
  </section>

  <section>
    <h2 class="abs sec-title" style="top:1218px">Fields of Interest</h2>
    <div class="abs sec-rule" style="top:1268px"></div>
    <p class="abs lead" style="top:1298px;left:100px;width:1000px">Nemo enim ipsam voluptatem quia voluptas sit aspernatur aut odit aut fugit, sed quia consequuntur magni dolores eos qui ratione voluptatem sequi nesciunt. Neque porro quisquam est, qui dolorem ipsum quia dolor sit amet, consectetur.</p>

    <div class="abs field-photo" style="left:107px;top:1388px;width:235px;background:linear-gradient(160deg,#c9a486,#8a5f45 60%,#3b2f2a)" role="img" aria-label="Team working around a table with laptop and papers"></div>
    <div class="abs field-photo" style="left:358px;top:1388px;width:233px;background:linear-gradient(180deg,#b9c3c8,#8c8474 50%,#5e5547)" role="img" aria-label="Climber in red jacket on a rocky mountain trail"></div>
    <div class="abs field-photo" style="left:610px;top:1388px;width:232px;background:linear-gradient(180deg,#d6c6cf,#a08a9a 50%,#7a3b2f)" role="img" aria-label="Hiker in red jacket looking over a misty valley"></div>
    <div class="abs field-photo" style="left:859px;top:1388px;width:235px;background:linear-gradient(160deg,#e6e6e6,#b8c2cc 55%,#7a8a99)" role="img" aria-label="Laptop and tablet showing colorful charts on a desk"></div>

    <div class="abs field-cap" style="left:124px;top:1619px;width:201px"><h3>Brand Marketing</h3><p>Nemo enim ipsam voluptatem quia voluptas sit aspernatur.</p></div>
    <div class="abs field-cap featured" style="left:373px;top:1619px;width:202px"><h3>Rock Climbing</h3><p>Nemo enim ipsam voluptatem quia voluptas sit aspernatur.</p></div>
    <div class="abs field-cap" style="left:625px;top:1619px;width:202px"><h3>Hiking &amp; Traveling</h3><p>Nemo enim ipsam voluptatem quia voluptas sit aspernatur.</p></div>
    <div class="abs field-cap" style="left:875px;top:1619px;width:202px"><h3>Exercising</h3><p>Nemo enim ipsam voluptatem quia voluptas sit aspernatur.</p></div>
  </section>

  <section>
    <div class="abs blog-panel"></div>
    <h2 class="abs panel-title" style="left:119px;top:1818px">Blogs &amp; Articles</h2>

    <div class="abs post-photo" style="left:119px;top:1890px;background:linear-gradient(160deg,#f2f2f2,#d9dde2 60%,#b9c4cf)" role="img" aria-label="Hand-drawn marketing strategy mind map on paper"><div class="post-tag blue">Brand Marketing</div></div>
    <div class="abs post-photo" style="left:451px;top:1890px;background:linear-gradient(160deg,#6a6a6a,#cfcac2 45%,#e8e4dc)" role="img" aria-label="Notebook with marketing sketches, coffee cup and markers"><div class="post-tag dark">Email Automation</div></div>
    <div class="abs post-photo" style="left:119px;top:2306px;background:linear-gradient(180deg,#9fb7c6,#5f6e5a 50%,#3b4a3e)" role="img" aria-label="Hiker crossing a mountain stream"><div class="post-tag dark">Hiking</div></div>
    <div class="abs post-photo" style="left:451px;top:2306px;background:linear-gradient(180deg,#3f74c0,#b9c8d6 45%,#7a6a58)" role="img" aria-label="Climbers on a snowy mountain ridge under blue sky"><div class="post-tag dark">Rock Climbing</div></div>

    <div class="abs post-meta" style="left:119px;top:2143px"><span><svg width="11" height="11" viewBox="0 0 11 11"><rect x=".5" y="1.5" width="10" height="9" fill="none" stroke="currentColor"/><rect x=".5" y="1.5" width="10" height="3" fill="currentColor"/></svg>Posted: 09-2-16</span><span><svg width="11" height="11" viewBox="0 0 11 11"><rect x=".5" y="1.5" width="10" height="9" fill="none" stroke="currentColor"/><rect x=".5" y="1.5" width="10" height="3" fill="currentColor"/></svg>Last Modified: 10-2-16</span></div>
    <div class="abs post-meta" style="left:451px;top:2143px"><span><svg width="11" height="11" viewBox="0 0 11 11"><rect x=".5" y="1.5" width="10" height="9" fill="none" stroke="currentColor"/><rect x=".5" y="1.5" width="10" height="3" fill="currentColor"/></svg>Posted: 09-2-16</span><span><svg width="11" height="11" viewBox="0 0 11 11"><rect x=".5" y="1.5" width="10" height="9" fill="none" stroke="currentColor"/><rect x=".5" y="1.5" width="10" height="3" fill="currentColor"/></svg>Last Modified: 10-2-16</span></div>
    <div class="abs post-meta" style="left:119px;top:2557px"><span><svg width="11" height="11" viewBox="0 0 11 11"><rect x=".5" y="1.5" width="10" height="9" fill="none" stroke="currentColor"/><rect x=".5" y="1.5" width="10" height="3" fill="currentColor"/></svg>Posted: 09-2-16</span><span><svg width="11" height="11" viewBox="0 0 11 11"><rect x=".5" y="1.5" width="10" height="9" fill="none" stroke="currentColor"/><rect x=".5" y="1.5" width="10" height="3" fill="currentColor"/></svg>Last Modified: 10-2-16</span></div>
    <div class="abs post-meta" style="left:451px;top:2557px"><span><svg width="11" height="11" viewBox="0 0 11 11"><rect x=".5" y="1.5" width="10" height="9" fill="none" stroke="currentColor"/><rect x=".5" y="1.5" width="10" height="3" fill="currentColor"/></svg>Posted: 09-2-16</span><span><svg width="11" height="11" viewBox="0 0 11 11"><rect x=".5" y="1.5" width="10" height="9" fill="none" stroke="currentColor"/><rect x=".5" y="1.5" width="10" height="3" fill="currentColor"/></svg>Last Modified: 10-2-16</span></div>

    <p class="abs post-text" style="left:119px;top:2167px">Nemo enim ipsam voluptatem quia voluptas sit aspernatur aut odit aut fugit, sed quia consequuntur magni dolores eos qui ratione voluptatem sequi nesciunt.</p>
    <p class="abs post-text" style="left:451px;top:2167px">Nemo enim ipsam voluptatem quia voluptas sit aspernatur aut odit aut fugit, sed quia consequuntur magni dolores eos qui ratione voluptatem sequi nesciunt.</p>
    <p class="abs post-text" style="left:119px;top:2581px">Nemo enim ipsam voluptatem quia voluptas sit aspernatur aut odit aut fugit, sed quia consequuntur magni dolores eos qui ratione voluptatem sequi nesciunt.</p>
    <p class="abs post-text" style="left:451px;top:2581px">Nemo enim ipsam voluptatem quia voluptas sit aspernatur aut odit aut fugit, sed quia consequuntur magni dolores eos qui ratione voluptatem sequi nesciunt.</p>

    <div class="abs read-btn blue" style="left:119px;top:2244px">Read More</div>
    <div class="abs read-btn dark" style="left:451px;top:2244px">Read More</div>
    <div class="abs read-btn dark" style="left:119px;top:2659px">Read More</div>
    <div class="abs read-btn dark" style="left:451px;top:2659px">Read More</div>

    <div class="abs pager"><span class="on">&lt;&lt; Prev</span><span class="on">1</span><span>2</span><span>3</span><span>4</span><span style="padding:0 22px">Next &gt;&gt;</span></div>

    <div class="abs side-panel"></div>
    <h2 class="abs panel-title" style="left:790px;width:308px;text-align:center;top:1810px;font-size:21px">Professional</h2>

    <div class="abs side-photo" style="top:1860px;background:linear-gradient(180deg,#c9d3dc,#8e97a0 55%,#4a4640)" role="img" aria-label="Person standing on a rock summit above clouds"></div>
    <p class="abs side-text" style="top:2026px">Nemo enim ipsam voluptatem quia voluptas sit aspernatur.</p>
    <div class="abs side-date" style="top:2085px"><svg width="12" height="12" viewBox="0 0 12 12"><circle cx="6" cy="6" r="5" fill="none" stroke="currentColor" stroke-width="1.5"/><path d="M6 3v3h2.5" fill="none" stroke="currentColor" stroke-width="1.5"/></svg>September 25, 2015</div>

    <div class="abs side-photo" style="top:2125px;background:linear-gradient(180deg,#b7c6d4,#e8ecef 50%,#3c3f44)" role="img" aria-label="Hiker with backpack facing snowy mountains"></div>
    <p class="abs side-text" style="top:2291px">Nemo enim ipsam voluptatem quia voluptas sit aspernatur.</p>
    <div class="abs side-date" style="top:2352px"><svg width="12" height="12" viewBox="0 0 12 12"><circle cx="6" cy="6" r="5" fill="none" stroke="currentColor" stroke-width="1.5"/><path d="M6 3v3h2.5" fill="none" stroke="currentColor" stroke-width="1.5"/></svg>September 25, 2015</div>

    <div class="abs side-photo" style="top:2391px;background:linear-gradient(160deg,#e9e3da,#a7a9ab 50%,#b4443e)" role="img" aria-label="Calculator, notebook and coffee cup on a desk"></div>
    <p class="abs side-text" style="top:2558px">Nemo enim ipsam voluptatem quia voluptas sit aspernatur.</p>
    <div class="abs side-date" style="top:2617px"><svg width="12" height="12" viewBox="0 0 12 12"><circle cx="6" cy="6" r="5" fill="none" stroke="currentColor" stroke-width="1.5"/><path d="M6 3v3h2.5" fill="none" stroke="currentColor" stroke-width="1.5"/></svg>September 25, 2015</div>

    <div class="abs" style="left:808px;top:2664px;width:272px;height:1px;background:#cfcfcf"></div>
    <h2 class="abs panel-title" style="left:790px;width:308px;text-align:center;top:2686px;font-size:20px">Social Media</h2>
    <div class="abs social"><span style="background:#3b5a98"></span><span style="background:#4aa3dd"></span><span style="background:#d6452f"></span><span style="background:#1e76b0"></span><span style="background:#d4322a"></span></div>
  </section>

  <section>
    <div class="abs subscribe-rule"></div>
    <h2 class="abs sec-title" style="top:2952px">Email Automation</h2>
    <div class="abs sec-rule" style="top:3006px"></div>
    <div class="abs email-input">Enter your email address</div>
    <div class="abs btn-blue subscribe-btn">Subscribe</div>
  </section>

  <footer>
    <svg class="abs footer-shape" width="1200" height="387" viewBox="0 0 1200 387" aria-hidden="true">
      <polygon points="0,40 570,10 930,40 1200,52 1200,387 0,387" fill="var(--footer)"/>
      <polygon points="0,38 190,32 260,44 0,50" fill="var(--blue)"/>
      <polygon points="760,26 930,40 935,56 820,40" fill="var(--blue)"/>
    </svg>
    <div class="abs footer-brand">ARIN SOLANO</div>
    <div class="abs footer-links">What is Bloom Path<i>|</i>Who I am<i>|</i>Brand Marketing<i>|</i>Email Automation<i>|</i>Hiking<i>|</i>Rock Climbing</div>
    <div class="abs footer-rule"></div>
    <div class="abs copyright">© 2017 Arin Solano. All Rights Reserved</div>
    <div class="abs footer-social"><span></span><span></span><span></span><span></span><span></span></div>
  </footer>

</div>
</body>
</html>
```